New Innovative Counselling and psychotherapy Service needs Business Card design

Keep it simple and professional. On one side, just company name and logo (perhaps in all blue) and maybe a tag line.

On other side (all white) my name and Qualifications in centre

Industry/Entity Type

Health And Wellness

Contact Information for Business Card

Dara Whelby
Counsellor & Psychotherapist
BSc (Psychol.), BA, Dip. (Couns. & Psych.), PG.Cert (CBT), FGTrK, ONRE

I will also require Mobile no, Email and web site address of which I'll pass on to final designer.

Font styles to use
Sans Serif

Requirements
Must have
• My Logo Only and please use the colours in logo that is in it.
Should not have
• Any other images

```html
<!DOCTYPE html>
<html lang="en">
<head>
<meta charset="utf-8">
<title>Brightwell Path – Business Card</title>
<link href="https://fonts.googleapis.com/css2?family=Raleway:wght@400;500&family=Open+Sans+Condensed:wght@300;700&family=Open+Sans:wght@400;600&display=swap" rel="stylesheet">
<style>
  :root {
    --backdrop: #2b2b2b;
    --card: #ffffff;
    --brand-blue: #4bb8ea;
    --brand-green: #9ccf62;
    --ink: #3d3d3d;
    --ink-soft: #6a6a6a;
    --wash-blue: #e8f4fb;
  }
  * { margin: 0; padding: 0; box-sizing: border-box; }
  html, body {
    width: 1200px; height: 900px; overflow: hidden;
    background: var(--backdrop);
  }
  .canvas {
    position: relative; width: 1200px; height: 900px;
    display: flex; flex-direction: column; align-items: center; justify-content: center;
    gap: 44px;
  }
  .card {
    position: relative; width: 640px; height: 366px;
    background: var(--card);
    overflow: hidden;
    box-shadow: 0 6px 18px rgba(0,0,0,.35);
  }

  /* Front */
  .front .brand {
    position: absolute; left: 120px; top: 118px;
    display: flex; align-items: center; gap: 22px;
  }
  .front .brand-dot {
    width: 74px; height: 74px; border-radius: 50%;
    background: var(--brand-blue);
  }
  .front .brand-name {
    font-family: "Raleway", sans-serif; font-weight: 400;
    font-size: 46px; color: var(--ink); letter-spacing: .3px;
  }
  .front .tagline {
    position: absolute; left: 0; right: 0; top: 268px; text-align: center;
    font-family: "Raleway", sans-serif; font-weight: 500;
    font-size: 15px; color: var(--ink-soft); letter-spacing: .2px;
  }

  /* Back */
  .back .wash {
    position: absolute; left: 245px; top: 40px;
    width: 290px; height: 290px; border-radius: 50%;
    background: var(--wash-blue);
  }
  .back .details {
    position: absolute; left: 0; right: 0; top: 92px;
    display: flex; flex-direction: column; align-items: center;
    font-family: "Open Sans Condensed", sans-serif;
  }
  .back .person {
    font-weight: 700; font-size: 26px; color: var(--brand-blue);
    letter-spacing: .5px; text-transform: uppercase;
  }
  .back .rule {
    width: 230px; height: 3px; background: var(--brand-green); margin: 4px 0 6px;
  }
  .back .role {
    font-weight: 300; font-size: 24px; color: var(--brand-green);
    text-transform: uppercase; letter-spacing: .4px;
  }
  .back .quals {
    font-weight: 300; font-size: 15px; color: var(--brand-green);
    text-align: center; line-height: 1.25; margin-top: 2px;
  }
  .back .contact {
    list-style: none; margin-top: 10px;
    font-family: "Open Sans", sans-serif; font-size: 17px; color: var(--ink);
    display: flex; flex-direction: column; align-items: flex-start; gap: 3px;
  }
  .back .contact li { display: flex; align-items: center; gap: 8px; }
  .back .contact svg { width: 16px; height: 16px; flex: none; }
</style>
</head>
<body>
<main class="canvas">
  <section class="card front" aria-label="Card front">
    <div class="brand">
      <span class="brand-dot" aria-hidden="true"></span>
      <span class="brand-name">Brightwell Path</span>
    </div>
    <p class="tagline">Caring For Your Psychological Well-Being Is Our Top Priority</p>
  </section>

  <section class="card back" aria-label="Card back">
    <div class="wash" aria-hidden="true"></div>
    <div class="details">
      <h1 class="person">Dara Whelby</h1>
      <div class="rule"></div>
      <p class="role">Counsellor &amp; Psychotherapist</p>
      <p class="quals">BSc (Psychol.), BA, Dip. (Couns. &amp; Psych.)<br>PG.Cert (CBT), FGTrK, ONRE</p>
      <ul class="contact">
        <li>
          <svg viewBox="0 0 16 16" aria-hidden="true"><rect x="4" y="1" width="8" height="14" rx="1.5" fill="var(--brand-blue)"/><rect x="5.5" y="3" width="5" height="8" fill="#fff"/></svg>
          555 014 2287
        </li>
        <li>
          <svg viewBox="0 0 16 16" aria-hidden="true"><rect x="1" y="3" width="14" height="10" rx="1" fill="var(--brand-blue)"/><path d="M1.5 3.8 8 9l6.5-5.2" fill="none" stroke="#fff" stroke-width="1.3"/></svg>
          dara@brightwellpath.com
        </li>
        <li>
          <svg viewBox="0 0 16 16" aria-hidden="true"><circle cx="8" cy="8" r="7" fill="var(--brand-blue)"/><path d="M1.5 8h13M8 1.2c-3 3.6-3 10 0 13.6M8 1.2c3 3.6 3 10 0 13.6" fill="none" stroke="#fff" stroke-width="1"/></svg>
          www.brightwellpath.com
        </li>
      </ul>
    </div>
  </section>
</main>
</body>
</html>
```